Personal Injury Law Firm needs folder design

Need a folder design for our personal injury law firm, Corrow & Talmidge, LLC. to give to all of our clients with their documents at the end of their case. I've attached our branding guide. We are branded as the 5 star law firm that fights for our clients like family. It should incorporate our colors or Green and White. We'd like to convey a message of moving on to the next chapter after finishing their case.

```html
<!DOCTYPE html>
<html lang="en">
<head>
<meta charset="utf-8">
<title>Corrow &amp; Talmidge, LLC. — Client Folder</title>
<link rel="stylesheet" href="https://fonts.googleapis.com/css2?family=Cinzel:wght@400;500&family=Lato:wght@300;400&display=swap">
<style>
  :root {
    --stage: #7c8280;
    --green-light: #2fbf8f;
    --green-mid: #12a97a;
    --green-deep: #058f58;
    --white: #ffffff;
    --fold-line: rgba(0, 0, 0, 0.12);
  }
  * { box-sizing: border-box; margin: 0; padding: 0; }
  html, body {
    width: 1200px;
    height: 900px;
    overflow: hidden;
    background: var(--stage);
  }
  .folder-spread {
    position: absolute;
    left: 60px;
    top: 90px;
    width: 1080px;
    height: 720px;
    display: flex;
  }
  .panel {
    position: relative;
    width: 540px;
    height: 720px;
    overflow: hidden;
  }
  .panel-back {
    background: linear-gradient(160deg, var(--green-mid) 0%, var(--green-light) 55%, var(--green-mid) 100%);
  }
  .panel-front {
    background: linear-gradient(200deg, var(--green-deep) 0%, var(--green-mid) 55%, var(--green-light) 100%);
    border-left: 1px solid var(--fold-line);
  }
  .texture {
    position: absolute;
    inset: 0;
    width: 100%;
    height: 100%;
  }
  .website {
    position: absolute;
    left: 0;
    right: 0;
    bottom: 70px;
    text-align: center;
    font-family: "Lato", sans-serif;
    font-weight: 300;
    font-size: 15px;
    letter-spacing: 2.5px;
    color: var(--white);
  }
  .firm-mark {
    position: absolute;
    left: 0;
    right: 0;
    top: 220px;
    display: flex;
    align-items: center;
    justify-content: center;
    gap: 14px;
  }
  .firm-square {
    width: 60px;
    height: 60px;
    background: var(--white);
    flex: none;
  }
  .firm-text {
    display: flex;
    flex-direction: column;
    gap: 6px;
  }
  .firm-name {
    font-family: "Cinzel", serif;
    font-weight: 400;
    font-size: 22px;
    letter-spacing: 1px;
    color: var(--white);
    white-space: nowrap;
  }
  .firm-tagline {
    font-family: "Cinzel", serif;
    font-weight: 400;
    font-size: 9px;
    letter-spacing: 3px;
    color: var(--white);
    text-align: right;
  }
</style>
</head>
<body>
  <main class="folder-spread">
    <section class="panel panel-back">
      <svg class="texture" viewBox="0 0 540 720" role="img" aria-label="Faint tonal pattern of rounded squares across the back cover">
        <defs>
          <radialGradient id="backGlow" cx="60%" cy="45%" r="60%">
            <stop offset="0" stop-color="#ffffff" stop-opacity="0.10"/>
            <stop offset="1" stop-color="#ffffff" stop-opacity="0"/>
          </radialGradient>
        </defs>
        <rect width="540" height="720" fill="url(#backGlow)"/>
      </svg>
      <p class="website">www.corrowandtalmidge.com</p>
    </section>
    <section class="panel panel-front">
      <svg class="texture" viewBox="0 0 540 720" role="img" aria-label="Faint tonal pattern of rounded squares across the front cover">
        <defs>
          <radialGradient id="frontGlow" cx="15%" cy="10%" r="70%">
            <stop offset="0" stop-color="#ffffff" stop-opacity="0.16"/>
            <stop offset="1" stop-color="#ffffff" stop-opacity="0"/>
          </radialGradient>
        </defs>
        <rect width="540" height="720" fill="url(#frontGlow)"/>
      </svg>
      <div class="firm-mark">
        <div class="firm-square"></div>
        <div class="firm-text">
          <span class="firm-name">Corrow &amp; Talmidge, LLC.</span>
          <span class="firm-tagline">Injury Attorneys</span>
        </div>
      </div>
    </section>
  </main>
</body>
</html>
```